International Petrochemical business needs a web design for Clearway Desk system

We need a web design for a "Clearway Desk" system for an international petrochemical company. The web site is used internally within the company. It is hosted by an internal department which provides government permit request service for other departments.

We would like to see designs of two pages using color light blue. (home page, internal page as attached).
Home Page:
1. Header has a background image and small animation. Header on home page can be taller than the header of the internal page.
2. Layout as attached.

Internal Page:
1. Header can use the same background image as the home page and can be shorter to utilize the page for content.
2. The blue icon behind every captions represent an icon. When user move mouse over this icon, it displays the caption in Thai language as a tooltip. This icon needs to be redesign.

The final design should communicate the followings:
- Excellent service provided system in terms of time and accurary
- Rapid growth of business via building petrochemical refinery plant
Updates

For Internal Page, the blue circle behind every captions represent an icon. When mouse over this icon, a tool tip showing the caption in Thai language is shown. Please also design this icon..

There are more feedbacks from customer as followed:

1. Banner should consists of 
    1.1 "Approved" stamp on paper
    1.2 An image of Garuda. It is used on every government documents in Thailand
    1.3 Image of petrochemical plant
2. Each menu item (Home, Permit, Search, etc) should have different colors. Drop down menu will use the same color as its parent menu item.
3. Overall tone of the web page should be light blue with background of the body the web page in white
4. "New Request" button should use green color with icon on it
5. Table header of each box in the body of the page should use dark blue background with text in white

Please kindly submit your revisions.
Thank you.

Industry/Entity Type

Business

Requirements
Must have
• 1. Design for 1024x768 screen resolution
2. Use light blue theme
3. Background of header where the company logo is must have white background

```html
<!DOCTYPE html>
<html lang="en">
<head>
<meta charset="utf-8">
<title>Clearway Desk – Home</title>
<link href="https://fonts.googleapis.com/css2?family=Ubuntu:wght@400;500;700&display=swap" rel="stylesheet">
<style>
:root{
  --blue:#3f9ff0;
  --blue-light:#6fb9f7;
  --blue-deep:#1e7fe0;
  --navy-text:#1b5fae;
  --dark:#333333;
  --dark-2:#444444;
  --grey-text:#8a8a8a;
  --row-text:#6a6a6a;
  --line:#d6d6d6;
  --red:#e23333;
  --red-dark:#b81f1f;
  --white:#ffffff;
}
*{box-sizing:border-box;margin:0;padding:0}
html,body{width:1182px;height:1200px;overflow:hidden;background:var(--white)}
body{position:relative;font-family:"Ubuntu",sans-serif;color:var(--row-text)}
.hero{position:absolute;left:0;top:0;width:1182px;height:660px;
  background:linear-gradient(180deg,#dcebf7 0%,#eef5fb 30%,#c9cfd6 55%,#9aa3ad 75%,#e6ebf0 92%,#ffffff 100%)}
.brand{position:absolute;left:131px;top:18px;display:flex;align-items:center;gap:8px}
.brand-dot{width:36px;height:36px;border-radius:50%;background:var(--blue-deep)}
.brand-name{font-weight:700;font-size:20px;color:var(--blue-deep);line-height:1}
.nav{position:absolute;left:129px;top:79px;width:923px;height:37px;border-radius:4px;
  background:linear-gradient(180deg,#8cc8fb,#4aa6f2);display:flex;align-items:center;padding-left:8px}
.nav a{color:var(--white);text-decoration:none;font-size:14px;width:102px;text-align:center;
  border-right:1px dashed rgba(255,255,255,.5)}
.nav a:last-of-type{border-right:0}
.search{position:absolute;right:8px;top:8px;width:282px;height:21px;background:var(--white);
  border:1px solid #b9d9f5;display:flex;align-items:center;justify-content:space-between;padding:0 6px;
  font-size:10px;font-style:italic;color:#999}
.panel{position:absolute;border-radius:4px;overflow:hidden;
  background:linear-gradient(180deg,#ffffff,#e9e9e9);box-shadow:0 2px 4px rgba(0,0,0,.15)}
.panel-head{background:var(--dark);color:var(--white);font-weight:500;font-size:18px;
  height:47px;line-height:47px;padding-left:12px;letter-spacing:-.3px}
.grid{width:calc(100% - 24px);margin:0 12px;border-collapse:collapse;font-size:13px}
.grid th{font-weight:400;font-size:16px;color:var(--grey-text);text-align:left;height:40px;padding-left:12px;
  border-bottom:1px dashed var(--line)}
.grid td{height:38px;padding-left:22px;border-bottom:1px dashed var(--line)}
.grid th+th,.grid td+td{border-left:1px solid #dcdcdc}
.pager{position:absolute;right:16px;bottom:10px;display:flex;align-items:center;gap:4px;font-size:15px;color:#aaa}
.pager .cur{color:var(--blue-deep)}
.pager .arrow{width:16px;height:16px;border:1px solid #999;background:#f4f4f4;display:flex;align-items:center;justify-content:center}
.pager .arrow svg{width:6px;height:8px}
.expiring{position:absolute;left:129px;top:655px;width:923px;height:194px;border-radius:4px;
  background:linear-gradient(180deg,#6ab7f7,#3e9bef);color:var(--white)}
.expiring h2{font-weight:500;font-size:19px;padding:10px 0 0 11px;height:40px;letter-spacing:-.3px}
.expiring .grid{border-top:1px dashed rgba(255,255,255,.5)}
.expiring .grid th{color:var(--white);border-bottom-color:rgba(255,255,255,.5)}
.expiring .grid td{padding-left:12px;border-bottom-color:rgba(255,255,255,.5);color:var(--white)}
.expiring .grid th+th,.expiring .grid td+td{border-left-color:rgba(255,255,255,.35)}
.expiring .pager{color:#bfe0ff}
.expiring .pager .cur{color:var(--white)}
.cta{position:absolute;left:622px;top:881px;width:410px;height:59px}
.cta-bar{position:absolute;left:0;top:2px;width:410px;height:56px;border-radius:3px;
  background:linear-gradient(180deg,#f04848,var(--red-dark));border-bottom:3px solid #9a1717}
.cta-bar span{position:absolute;left:98px;top:8px;font-size:36px;font-weight:500;color:var(--white);letter-spacing:-.5px}
.cta-ribbon{position:absolute;left:18px;top:-4px;width:64px;height:78px}
.recent{position:absolute;left:628px;top:967px;width:404px;height:166px;border-radius:4px;background:var(--dark-2);color:var(--white)}
.recent-tab{position:absolute;left:-4px;top:0;width:340px;height:30px;line-height:30px;padding-left:12px;font-size:15px;font-weight:500;
  background:linear-gradient(180deg,#7ec1fa,#4aa6f2);clip-path:polygon(0 0,100% 0,94% 100%,0 100%)}
.recent .grid{position:absolute;top:49px;left:0;border-top:1px solid #5c5c5c}
.recent .grid th{color:#e6e6e6;padding-left:10px;border-bottom:1px solid #5c5c5c}
.recent .grid td{padding-left:10px;color:var(--white);border-bottom:1px solid #5c5c5c}
.recent .grid th+th,.recent .grid td+td{border-left-color:#5c5c5c}
.recent .pager{color:#aaa}
.recent .pager .cur{color:var(--white)}
.footer-rule{position:absolute;left:129px;top:1152px;width:923px;border-top:1px dashed #bbb}
.copyright{position:absolute;left:132px;top:1171px;font-size:11px;color:#666;letter-spacing:-.2px}
.footer-brand{position:absolute;right:130px;top:1166px;display:flex;align-items:center;gap:5px;font-size:11px;font-weight:700;color:#777}
.footer-brand i{width:20px;height:20px;border-radius:50%;background:#888;display:block}
</style>
</head>
<body>
<div class="hero" role="img" aria-label="Petrochemical refinery plant with towers and pipework under a bright sky"></div>

<header>
  <div class="brand"><span class="brand-dot"></span><span class="brand-name">Northbay Petrochemical</span></div>
  <nav class="nav">
    <a href="#">Home</a><a href="#">Permits</a><a href="#">Search</a><a href="#">Report</a><a href="#">Admin</a><a href="#">Help</a>
    <div class="search">Serch By Number...
      <svg width="14" height="14" viewBox="0 0 14 14"><circle cx="5.5" cy="5.5" r="4" fill="none" stroke="#555" stroke-width="2"/><line x1="8.5" y1="8.5" x2="13" y2="13" stroke="#555" stroke-width="2.4"/></svg>
    </div>
  </nav>
</header>

<section class="panel" style="left:129px;top:433px;width:456px;height:198px">
  <h2 class="panel-head">NEW REQUESTS</h2>
  <table class="grid">
    <tr><th style="width:117px">Request No.</th><th style="width:164px">Requested Date</th><th>Branch</th></tr>
    <tr><td>56-0003</td><td style="padding-left:52px">20/4/2013</td><td style="padding-left:36px">GC1</td></tr>
    <tr><td>56-0004</td><td style="padding-left:52px">21/4/2013</td><td style="padding-left:36px">GC2</td></tr>
  </table>
  <div class="pager"><span class="arrow"><svg viewBox="0 0 6 8"><path d="M6 0L0 4 6 8z" fill="#333"/></svg></span><span class="cur">1</span> 2 3 4 5 6 7<span class="arrow"><svg viewBox="0 0 6 8"><path d="M0 0L6 4 0 8z" fill="#333"/></svg></span></div>
</section>

<section class="panel" style="left:596px;top:432px;width:456px;height:199px">
  <h2 class="panel-head">MY WORKING REQUESTS</h2>
  <table class="grid">
    <tr><th style="width:117px">Request No.</th><th style="width:162px">Requested Date</th><th>Status</th></tr>
    <tr><td>55-0200</td><td style="padding-left:52px">25/3/2013</td><td>Waiting for process</td></tr>
    <tr><td>55-0210</td><td style="padding-left:52px">23/3/2013</td><td>In progress</td></tr>
  </table>
  <div class="pager"><span class="arrow"><svg viewBox="0 0 6 8"><path d="M6 0L0 4 6 8z" fill="#333"/></svg></span><span class="cur">1</span> 2 3 4 5 6 7<span class="arrow"><svg viewBox="0 0 6 8"><path d="M0 0L6 4 0 8z" fill="#333"/></svg></span></div>
</section>

<section class="expiring">
  <h2>Expiring Permits</h2>
  <table class="grid">
    <tr><th style="width:105px">Permit No.</th><th style="width:148px">Expire Date</th><th style="width:182px">Permit Name</th><th style="width:139px">Branch</th><th style="width:186px">Required Time (Day)</th><th>Due Date</th></tr>
    <tr><td>56-0003</td><td>20/4/2013</td><td>Permit Name ###10</td><td>GC1</td><td>30 Days</td><td>- 40 Days</td></tr>
    <tr><td>56-0004</td><td>21/4/2013</td><td>Permit Name ###10</td><td>GC2</td><td>60 Days</td><td>- 15 Days</td></tr>
  </table>
  <div class="pager"><span class="arrow"><svg viewBox="0 0 6 8"><path d="M6 0L0 4 6 8z" fill="#333"/></svg></span><span class="cur">1</span> 2 3 4 5 6 7<span class="arrow"><svg viewBox="0 0 6 8"><path d="M0 0L6 4 0 8z" fill="#333"/></svg></span></div>
</section>

<section class="panel" style="left:129px;top:880px;width:456px;height:253px">
  <h2 class="panel-head">MY IN PROGRESS REQUESTS</h2>
  <table class="grid">
    <tr><th style="width:117px">Request No.</th><th style="width:164px">Requested Date</th><th>Status</th></tr>
    <tr><td>56-0001</td><td style="padding-left:52px">20/4/2013</td><td>In progress</td></tr>
    <tr><td>56-0002</td><td style="padding-left:52px">21/4/2013</td><td>In progress</td></tr>
    <tr><td>56-0002</td><td style="padding-left:52px">21/4/2013</td><td>In progress</td></tr>
  </table>
  <div class="pager"><span class="arrow"><svg viewBox="0 0 6 8"><path d="M6 0L0 4 6 8z" fill="#333"/></svg></span><span class="cur">1</span> 2 3 4 5 6 7<span class="arrow"><svg viewBox="0 0 6 8"><path d="M0 0L6 4 0 8z" fill="#333"/></svg></span></div>
</section>

<a class="cta" href="#" aria-label="New requests">
  <div class="cta-bar"><span>NEW REQUESTS</span></div>
  <svg class="cta-ribbon" viewBox="0 0 64 78">
    <path d="M0 0H64V78L32 62 0 78z" fill="#3a3a3a"/>
    <path d="M20 14h16l8 8v22H20z" fill="none" stroke="#fff" stroke-width="2.5"/>
    <path d="M36 14v8h8" fill="none" stroke="#fff" stroke-width="2.5"/>
    <path d="M26 36l10-10 4 4-10 10h-4z" fill="#fff"/>
  </svg>
</a>

<section class="recent">
  <h2 class="recent-tab">Recent Completed Requests</h2>
  <table class="grid">
    <tr><th style="width:143px">Request No.</th><th>Complete Date</th></tr>
    <tr><td>56-0001</td><td>20/4/2013</td></tr>
  </table>
  <div class="pager"><span class="arrow"><svg viewBox="0 0 6 8"><path d="M6 0L0 4 6 8z" fill="#333"/></svg></span><span class="cur">1</span> 2 3 4 5 6 7<span class="arrow"><svg viewBox="0 0 6 8"><path d="M0 0L6 4 0 8z" fill="#333"/></svg></span></div>
</section>

<footer>
  <div class="footer-rule"></div>
  <p class="copyright">Copyright © 2013 Northbay Petrochemical. All rights reserved.</p>
  <div class="footer-brand"><i></i>Northbay Petrochemical</div>
</footer>
</body>
</html>
```